Professional & attention grabbing.

A business card design, front and back. I already have a logo I will attach, but I am open to something new as well.
Things to include:
Name:
Title:
Phone:
Email:
Wanting something that is professional but attention grabbing.
Also we do a lot of work using drones on natural gas pipelines (leading the future)if you want to include any of that. I'm open to ideas.
Target Market(s)
Natural gas transmission industry / greenhouse gas mitigation industry
Industry/Entity Type
Business
Colors
Designer to choose colors to be used in the design.
Look and feel
Each slider illustrates characteristics of the customer's brand and the style your logo design should communicate.

```html
<!DOCTYPE html>
<html lang="en">
<head>
<meta charset="utf-8">
<title>Ridgeline Inspections – Business Card</title>
<link rel="stylesheet" href="https://fonts.googleapis.com/css2?family=Roboto:wght@400;500;700;900&family=Roboto+Condensed:wght@400&display=swap">
<style>
  :root {
    --page-bg: #e9e7e4;
    --card-bg: #f4f3f1;
    --ink-dark: #232325;
    --ink-text: #2d2d2f;
    --brand-red: #a3161f;
  }
  * { margin: 0; padding: 0; box-sizing: border-box; }
  html, body { width: 1200px; height: 969px; overflow: hidden; }
  body {
    background: var(--page-bg);
    font-family: "Roboto", Arial, sans-serif;
    position: relative;
  }
  .business-card {
    position: absolute;
    left: 100px;
    top: 198px;
    width: 1000px;
    height: 572px;
    background: var(--card-bg);
    border-radius: 26px;
    overflow: hidden;
    box-shadow: 0 10px 30px rgba(0,0,0,0.18);
  }
  .card-swoosh { position: absolute; inset: 0; width: 100%; height: 100%; }
  .company-mark {
    position: absolute;
    left: 72px;
    top: 70px;
    display: flex;
    align-items: center;
    gap: 18px;
  }
  .company-mark__square {
    width: 64px;
    height: 64px;
    background: var(--brand-red);
  }
  .company-mark__name {
    font-weight: 900;
    font-size: 52px;
    letter-spacing: -1px;
    color: var(--ink-dark);
    line-height: 1;
  }
  .company-tagline {
    position: absolute;
    left: 154px;
    top: 144px;
    font-family: "Roboto Condensed", Arial, sans-serif;
    font-size: 21px;
    color: var(--ink-dark);
    letter-spacing: 0.5px;
  }
  .person-name {
    position: absolute;
    left: 72px;
    top: 282px;
    font-weight: 700;
    font-size: 34px;
    letter-spacing: 1px;
    color: var(--brand-red);
  }
  .person-title {
    position: absolute;
    left: 72px;
    top: 334px;
    font-size: 27px;
    color: var(--ink-text);
  }
  .contact-list {
    position: absolute;
    left: 72px;
    top: 410px;
    list-style: none;
  }
  .contact-list li {
    display: flex;
    align-items: center;
    gap: 14px;
    height: 40px;
    font-size: 27px;
    color: var(--ink-text);
  }
  .contact-icon { width: 22px; height: 22px; fill: var(--brand-red); flex: none; }
</style>
</head>
<body>
  <div class="business-card">
    <svg class="card-swoosh" viewBox="0 0 1000 572" aria-hidden="true">
      <path fill="var(--brand-red)" transform="translate(-30 0)" d="M800 0 C880 10 860 160 770 285 C690 395 610 480 555 572 L1030 572 L1030 0 Z"/>
      <path fill="var(--card-bg)" transform="translate(-14 0)" d="M800 0 C880 10 860 160 770 285 C690 395 610 480 555 572 L1014 572 L1014 0 Z"/>
      <path fill="var(--ink-dark)" d="M800 0 C880 10 860 160 770 285 C690 395 610 480 555 572 L1000 572 L1000 0 Z"/>
    </svg>

    <div class="company-mark">
      <span class="company-mark__square"></span>
      <span class="company-mark__name">RIDGELINE</span>
    </div>
    <div class="company-tagline">INSPECTIONS</div>

    <h1 class="person-name">DANIEL HARPER</h1>
    <p class="person-title">CEO/Founder</p>

    <ul class="contact-list">
      <li>
        <svg class="contact-icon" viewBox="0 0 24 24"><path d="M6.6 10.8a15.1 15.1 0 0 0 6.6 6.6l2.2-2.2c.3-.3.7-.4 1-.2 1.1.4 2.3.6 3.6.6.6 0 1 .4 1 1V20c0 .6-.4 1-1 1C10.6 21 3 13.4 3 4c0-.6.4-1 1-1h3.5c.6 0 1 .4 1 1 0 1.3.2 2.5.6 3.6.1.3 0 .7-.2 1z"/></svg>
        <span>555 210 4187</span>
      </li>
      <li>
        <svg class="contact-icon" viewBox="0 0 24 24"><path d="M2 5h20v14H2z M3 6l9 7 9-7" fill="var(--brand-red)"/><path d="M3 6.5l9 6.5 9-6.5" fill="none" stroke="var(--card-bg)" stroke-width="1.6"/></svg>
        <span>daniel@ridgelineinspect.com</span>
      </li>
      <li>
        <svg class="contact-icon" viewBox="0 0 24 24"><circle cx="12" cy="12" r="10"/><path d="M2 12h20M12 2c3 3 3 17 0 20M12 2c-3 3-3 17 0 20" fill="none" stroke="var(--card-bg)" stroke-width="1.5"/></svg>
        <span>www.ridgelineinspect.com</span>
      </li>
    </ul>
  </div>
</body>
</html>
```